Request for Business Card Design

Hi. My name is Marlene, I am looking for a new business card design for my company, Quarrow Signal Instruments, LLC. I really like the design you did for Tarsel Venture and was hoping you could do something similar using our full logo and our mark. I am also open to any raised texture design using our mark. I have attached our full logo, which would need to be somewhere on the card, as well as the mark in both outline and full form, as well as our brand colors / guide. The card does not have to be white, as long as our logo and mark appear. I actually like darker colored business cards more, but am open to all options. If you are interested in working with me, please let me know. We would also take the business card design into letterhead design if you can do that.

```html
<!DOCTYPE html>
<html lang="en">
<head>
<meta charset="utf-8">
<title>Quarrow Signal Instruments — Business Card</title>
<link href="https://fonts.googleapis.com/css2?family=Lato:wght@400;700;900&display=swap" rel="stylesheet">
<style>
  :root {
    --stage: #1c1c1e;
    --card-dark: #3b3b3d;
    --card-light: #ffffff;
    --brand-blue: #0f9cc8;
    --ink: #2b2b2d;
    --on-dark: #d9d9db;
  }
  * { box-sizing: border-box; margin: 0; padding: 0; }
  html, body {
    width: 1200px; height: 875px; overflow: hidden;
    background: var(--stage);
    font-family: "Lato", Arial, sans-serif;
  }
  .stage {
    position: relative; width: 1200px; height: 875px;
    display: flex; align-items: center; justify-content: center; gap: 50px;
  }
  .card {
    position: relative; width: 525px; height: 300px; border-radius: 18px;
    overflow: hidden; flex: none;
    box-shadow: 0 20px 40px rgba(0,0,0,.45);
  }
  .brand { display: flex; align-items: center; gap: 16px; }
  .brand__dot { border-radius: 50%; background: var(--brand-blue); flex: none; }
  .brand__name {
    font-weight: 900; text-transform: uppercase; line-height: 1; letter-spacing: .04em;
    white-space: nowrap;
  }
  /* Back */
  .card--back {
    background: var(--card-dark);
    display: flex; align-items: center; justify-content: center;
    padding: 0 48px;
  }
  .card--back .brand__dot { width: 40px; height: 40px; }
  .card--back .brand__name { color: var(--on-dark); font-size: 20px; }
  /* Front */
  .card--front { background: var(--card-light); color: var(--ink); }
  .card--front .brand { position: absolute; top: 36px; right: 34px; gap: 10px; }
  .card--front .brand__dot { width: 24px; height: 24px; }
  .card--front .brand__name { color: var(--ink); font-size: 14px; }
  .rule { position: absolute; height: 1px; background: var(--brand-blue); }
  .rule--top { top: 100px; right: 34px; width: 230px; }
  .address {
    position: absolute; top: 116px; right: 34px; text-align: right;
    font-size: 13px; line-height: 1.5; font-style: normal;
  }
  .address__web { color: var(--brand-blue); }
  .person { position: absolute; left: 34px; bottom: 112px; }
  .person__name { color: var(--brand-blue); font-weight: 900; font-size: 24px; text-transform: uppercase; line-height: 1.05; }
  .person__role { font-size: 15px; }
  .rule--bottom { left: 34px; bottom: 100px; width: 260px; }
  .contacts { position: absolute; left: 34px; bottom: 26px; list-style: none; font-size: 13px; line-height: 1.6; }
  .contacts li { display: flex; align-items: center; gap: 9px; }
  .contacts svg { width: 12px; height: 12px; fill: var(--brand-blue); flex: none; }
</style>
</head>
<body>
<main class="stage">
  <section class="card card--back" aria-label="Card back">
    <div class="brand">
      <span class="brand__dot"></span>
      <span class="brand__name">Quarrow Signal Instruments</span>
    </div>
  </section>

  <section class="card card--front" aria-label="Card front">
    <div class="brand">
      <span class="brand__dot"></span>
      <span class="brand__name">Quarrow Signal Instruments</span>
    </div>
    <div class="rule rule--top"></div>
    <address class="address">
      1180 Meridian Park Drive<br>
      Fairhaven, CO 80611<br>
      <span class="address__web">www.quarrowsignal.com</span>
    </address>

    <div class="person">
      <p class="person__name">Daniel Hart</p>
      <p class="person__role">Founder &amp; CEO</p>
    </div>
    <div class="rule rule--bottom"></div>
    <ul class="contacts">
      <li><svg viewBox="0 0 24 24"><path d="M6.6 10.8a15.1 15.1 0 0 0 6.6 6.6l2.2-2.2a1 1 0 0 1 1-.25 11.4 11.4 0 0 0 3.6.57 1 1 0 0 1 1 1V20a1 1 0 0 1-1 1A17 17 0 0 1 3 4a1 1 0 0 1 1-1h3.5a1 1 0 0 1 1 1c0 1.25.2 2.45.57 3.57a1 1 0 0 1-.25 1z"/></svg>+001 555 210 4832</li>
      <li><svg viewBox="0 0 24 24"><path d="M6 2h12v5H6zM4 8h16a2 2 0 0 1 2 2v7h-4v5H6v-5H2v-7a2 2 0 0 1 2-2zm4 9v3h8v-3z"/></svg>+001 555 210 4833</li>
      <li><svg viewBox="0 0 24 24"><path d="M2 5h20v14H2zm2 2v.5l8 5 8-5V7z"/></svg>Marlene@quarrowsignal.com</li>
    </ul>
  </section>
</main>
</body>
</html>
```